HOT TUB - SPAS service needs an business card

I need an business for my company who his specialise in a maintenance,water treatment and cleaning of Hot Tub - Spas for commercial and residential customers. The company operate mainly in the ski resort of Chamonix, Megève and St Gervais. The final product should communicate pure water, cleanest and professional for luxury property's.
I have upload a logo but any improvement on it is welcome.(color,size, details etc..) or any other idea. Thank you
Company Name: 58 BAINS
My name: Lucien Marchetti
Email: lucimarch@examplemail.net
Tel: +33 (0)6 71 58 29 64
Description to be on the card in french(first langage) and in English:
- Spas service
- Entretien, traitement eau, nettoyage.
- Maintenance, water treatment, cleaning.
Industry/Entity Type
Residential
Colors
Designer to choose colors to be used in the design.
Look and feel
Each slider illustrates characteristics of the customer's brand and the style your logo design should communicate.

```html
<!DOCTYPE html>
<html lang="fr">
<head>
<meta charset="utf-8">
<title>58 BAINS – cartes de visite</title>
<link rel="stylesheet" href="https://fonts.googleapis.com/css2?family=Open+Sans:wght@400;600;700&display=swap">
<style>
  :root {
    --page: #ebe8e4;
    --water-deep: #1a86d8;
    --water-mid: #2b9ae6;
    --water-light: #4cb3f2;
    --ink: #ffffff;
    --tab-red: #a8161c;
    --tab-red-light: #d0262c;
    --tab-blue: #1d7fd0;
  }
  * { box-sizing: border-box; margin: 0; padding: 0; }
  html, body {
    width: 1200px; height: 1039px; overflow: hidden;
    background: var(--page);
    font-family: "Open Sans", Arial, sans-serif;
    color: var(--ink);
  }
  .card {
    position: absolute;
    width: 824px; height: 472px;
    overflow: hidden;
    background: var(--water-mid);
    box-shadow: 0 4px 14px rgba(0,0,0,.18);
  }
  .card--front { left: 297px; top: 28px; }
  .card--back  { left: 44px;  top: 541px; }
  .water-texture {
    position: absolute; inset: 0;
    background:
      radial-gradient(ellipse at 70% 30%, var(--water-light) 0%, transparent 60%),
      radial-gradient(ellipse at 15% 85%, var(--water-deep) 0%, transparent 65%),
      linear-gradient(160deg, var(--water-mid), var(--water-deep));
  }
  .brand-mark {
    position: absolute;
    font-weight: 700;
    font-size: 64px;
    letter-spacing: 4px;
    line-height: 1;
  }
  .card--front .brand-mark { left: 180px; top: 98px; }
  .card--back  .brand-mark { left: 0; right: 0; text-align: center; top: 140px; }

  .tab { position: absolute; }
  .tab--red {
    left: 0; top: 258px; width: 14px; height: 184px;
    background: linear-gradient(90deg, var(--tab-red), var(--tab-red-light));
    border-radius: 0 10px 10px 0;
  }
  .tab--blue {
    right: 0; top: 316px; width: 12px; height: 70px;
    background: var(--tab-blue);
    border-radius: 10px 0 0 10px;
  }
  .company {
    position: absolute; left: 24px; top: 268px;
    font-size: 37px; font-weight: 600; line-height: 1;
  }
  .contact {
    position: absolute; left: 24px;
    display: flex; align-items: center; gap: 12px;
    font-size: 26px; line-height: 1;
  }
  .contact--phone { top: 343px; }
  .contact--mail  { top: 393px; }
  .contact svg { width: 24px; height: 24px; flex: none; }
  .holder {
    position: absolute; right: 30px; top: 338px;
    font-size: 33px; font-weight: 700; line-height: 1;
  }
  .services {
    position: absolute; left: 0; right: 0; top: 330px;
    text-align: center; line-height: 1;
  }
  .services__title { font-size: 28px; font-weight: 600; margin-bottom: 18px; }
  .services__list { font-size: 27px; margin-bottom: 12px; }
</style>
</head>
<body>

<section class="card card--front">
  <div class="water-texture" role="img" aria-label="Fond photographique de gouttes d'eau sur surface bleue"></div>
  <div class="brand-mark">58 BAINS</div>
  <div class="tab tab--red"></div>
  <div class="tab tab--blue"></div>
  <h1 class="company">58 BAINS</h1>
  <p class="contact contact--phone">
    <svg viewBox="0 0 24 24" aria-hidden="true"><path fill="none" stroke="#fff" stroke-width="2" d="M6 3c-2 1-3 3-2 6 2 5 6 9 11 11 3 1 5 0 6-2l-3-3-3 2c-3-1-6-4-7-7l2-3z"/></svg>
    <span>+33 (0)6 71 58 29 64</span>
  </p>
  <p class="contact contact--mail">
    <svg viewBox="0 0 24 24" aria-hidden="true"><path fill="#fff" d="M2 9l10-6 10 6v12H2z"/><path fill="none" stroke="#2b9ae6" stroke-width="1.8" d="M2 9l10 7 10-7"/></svg>
    <span>lucimarch@examplemail.net</span>
  </p>
  <p class="holder">Lucien Marchetti</p>
</section>

<section class="card card--back">
  <div class="water-texture" role="img" aria-label="Fond photographique de gouttes d'eau sur surface bleue"></div>
  <div class="brand-mark">58 BAINS</div>
  <div class="services">
    <h2 class="services__title">SPAS SERVICES</h2>
    <p class="services__list">•Entretien &nbsp;•traitement eau &nbsp;•nettoyage</p>
    <p class="services__list">•Maintenance &nbsp;•water treatment &nbsp;•cleaning.</p>
  </div>
</section>

</body>
</html>
```